Redesign Website - Current one too plain

The description is in the uploaded file. Please let me know if you need any more information. I'd prefer it if someone could implement the design to a WordPress site but the best design will win, regardless.
I would like the forms to look nice as well
UPDATE:
I don't think we can use the images that I provided, I think they make the site look a bit 'cheap' and I really don't know how to replace them. One thought I have had is to make the "Simple, Unique, Effective" a second feature on the right side of the page with the search on the left
Target Market(s)
Small companies, private sellers of cars and people who rent their caravan/holiday home out
Industry/Entity Type
Advertising
Number of Pages Required
3 page
Colors
Designer to choose colors to be used in the design.
Look and feel
Each slider illustrates characteristics of the customer's brand and the style your logo design should communicate.

```html
<!DOCTYPE html>
<html lang="en">
<head>
<meta charset="utf-8">
<title>Contact Us – Blotva</title>
<link href="https://fonts.googleapis.com/css2?family=Poppins:wght@400;500;600;700;800&display=swap" rel="stylesheet">
<style>
  :root {
    --lime: #dcfb00;
    --ink: #222222;
    --muted: #8a8a8a;
    --field: #f2f2f2;
    --white: #ffffff;
    --rule: #dddddd;
  }
  * { box-sizing: border-box; margin: 0; padding: 0; }
  html, body { width: 1200px; height: 985px; overflow: hidden; }
  body { font-family: "Poppins", sans-serif; color: var(--ink); background: var(--white); position: relative; }

  .site-header { position: absolute; top: 0; left: 0; width: 1200px; height: 101px; }
  .brand { position: absolute; left: 89px; top: 20px; display: flex; align-items: center; gap: 12px; }
  .brand-dot { width: 44px; height: 44px; border-radius: 50%; background: var(--lime); }
  .brand-name { font-size: 32px; font-weight: 600; letter-spacing: 6px; color: var(--ink); }

  .main-nav { position: absolute; right: 89px; top: 23px; display: flex; align-items: center; height: 43px; }
  .nav-item { display: flex; align-items: center; gap: 7px; font-size: 12.5px; font-weight: 500; text-transform: uppercase; padding: 0 22px; height: 26px; border-right: 1px solid #e4e4e4; color: var(--ink); text-decoration: none; }
  .nav-item:last-of-type { border-right: none; }
  .nav-item svg { width: 18px; height: 18px; }
  .nav-cta { margin-left: 4px; background: var(--lime); border-radius: 5px; height: 43px; width: 203px; display: flex; align-items: center; justify-content: center; font-size: 12.5px; font-weight: 700; text-transform: uppercase; color: var(--ink); text-decoration: none; }

  .hero { position: absolute; top: 101px; left: 0; width: 1200px; height: 607px;
    background: linear-gradient(180deg, #e2e2f4 0%, #e6e4ee 30%, #b9a88f 62%, #8a8a88 85%, #6f7070 100%); }
  .hero-title { position: absolute; top: 168px; width: 1200px; text-align: center; font-size: 41px; font-weight: 700; color: var(--ink); }
  .hero-lead { position: absolute; top: 225px; width: 1200px; text-align: center; font-size: 14px; color: var(--ink); }

  .contact-card { position: absolute; left: 307px; top: 284px; width: 586px; height: 518px; background: var(--white); border-radius: 27px; box-shadow: 0 30px 60px rgba(0,0,0,0.06); padding: 51px 45px 0; }
  .field-label { display: block; font-size: 10.5px; font-weight: 500; text-transform: uppercase; margin-bottom: 7px; }
  .field-label .req { color: var(--lime); }
  .field-input { width: 100%; height: 41px; background: var(--field); border: none; border-radius: 6px; padding: 0 20px; font-family: inherit; font-size: 12.5px; color: var(--muted); display: flex; align-items: center; }
  .field-group { margin-bottom: 13px; }
  .field-row { display: flex; gap: 8px; }
  .field-row .field-group { flex: 1; }
  .field-textarea { height: 132px; align-items: flex-start; padding-top: 12px; }
  .char-count { text-align: right; font-size: 12.5px; color: var(--muted); margin-top: -2px; }
  .submit-btn { display: block; margin: 24px auto 0; width: 136px; height: 46px; background: var(--lime); border: none; border-radius: 5px; box-shadow: 0 2px 0 #b7d000; font-family: inherit; font-size: 14px; font-weight: 700; text-transform: uppercase; color: var(--ink); }

  .site-footer { position: absolute; left: 89px; top: 918px; width: 1022px; border-top: 1px solid var(--rule); }
  .copyright { text-align: center; font-size: 14px; font-weight: 500; margin-top: 21px; }
  .back-to-top { position: absolute; left: 1136px; top: 898px; width: 40px; height: 40px; background: #111; border-radius: 4px; display: flex; align-items: center; justify-content: center; }
</style>
</head>
<body>
  <header class="site-header">
    <div class="brand"><span class="brand-dot"></span><span class="brand-name">BLOTVA</span></div>
    <nav class="main-nav">
      <a class="nav-item" href="#"><svg viewBox="0 0 24 24"><path d="M3 11 12 3l9 8h-3v9h-4v-6h-4v6H6v-9z" fill="#222"/></svg>Home</a>
      <a class="nav-item" href="#"><svg viewBox="0 0 24 24" fill="none" stroke="#222" stroke-width="1.6"><rect x="5" y="3" width="15" height="18" rx="1"/><circle cx="12.5" cy="10" r="2.5"/><path d="M8.5 17c.5-2.5 2-3.5 4-3.5s3.5 1 4 3.5M3 7h3M3 12h3M3 17h3"/></svg>Contact</a>
      <a class="nav-item" href="#"><svg viewBox="0 0 24 24" fill="none" stroke="#222" stroke-width="1.6"><circle cx="10" cy="8" r="4"/><path d="M3 21c0-4 3-7 7-7M14 20l6-6 2 2-6 6h-2z"/></svg>Register</a>
      <a class="nav-item" href="#"><svg viewBox="0 0 24 24" fill="none" stroke="#222" stroke-width="1.6"><circle cx="12" cy="8" r="4"/><path d="M4 21c0-4 3.5-7 8-7s8 3 8 7z"/></svg>Login</a>
      <a class="nav-cta" href="#">Advertise your company</a>
    </nav>
  </header>

  <section class="hero" role="img" aria-label="Photo of a motorway with a white delivery van at the roadside under a pale sky">
  </section>
  <h1 class="hero-title">Contact Us</h1>
  <p class="hero-lead">We can help, our team of experts is on hand to answer your questions.</p>

  <form class="contact-card">
    <div class="field-group">
      <label class="field-label">Name<span class="req">*</span></label>
      <div class="field-input">Enter your name</div>
    </div>
    <div class="field-row">
      <div class="field-group">
        <label class="field-label">Email<span class="req">*</span></label>
        <div class="field-input">Enter your email</div>
      </div>
      <div class="field-group">
        <label class="field-label">Phone<span class="req">*</span></label>
        <div class="field-input">Enter your phone number</div>
      </div>
    </div>
    <div class="field-group">
      <label class="field-label">Message<span class="req">*</span></label>
      <div class="field-input field-textarea">Type your text</div>
    </div>
    <p class="char-count">0 of 4000 max characters</p>
    <button class="submit-btn" type="button">Submit</button>
  </form>

  <footer class="site-footer">
    <p class="copyright">© Copyright 2023 Blotva. All Rights Reserved</p>
  </footer>
  <a class="back-to-top" href="#"><svg width="10" height="8" viewBox="0 0 10 8"><path d="M2 6 5 3l3 3" stroke="#dcfb00" stroke-width="1.6" fill="none"/></svg></a>
</body>
</html>
```